Help me make landing pages for my web application that are mobile friendly

I need to make 2 mobile friendly landing pages for an application. The 2 pages will be related. First I need a home page and then I need a working page. I do not want to change the color scheme or logos. Just layout and design.

```html
<!DOCTYPE html>
<html lang="en">
<head>
<meta charset="utf-8">
<title>Substitute Assignments – Mobile Screens</title>
<link href="https://fonts.googleapis.com/css2?family=Poppins:wght@400;500;600&display=swap" rel="stylesheet">
<style>
:root{
  --stage:#6a52a5;
  --white:#ffffff;
  --ink:#1d1b22;
  --muted:#6c6a72;
  --purple:#6b4fa8;
  --purple-soft:#e9e3f7;
  --nav-bg:#f7f4fd;
  --line:#e4e2ea;
  --help:#22a6d6;
  --green:#2aa44a;
  --blue:#1a7cf5;
  --red:#e0303a;
  --close:#e50914;
}
*{box-sizing:border-box;margin:0;padding:0}
html,body{width:1200px;height:1008px;overflow:hidden;background:var(--stage)}
body{font-family:"Poppins",sans-serif;color:var(--ink)}
.stage{position:absolute;left:0;top:0;width:1489px;height:1251px;transform:scale(.8059);transform-origin:0 0}
.screen{position:absolute;top:109px;width:390px;background:var(--white);overflow:hidden}
.screen.assign{height:846px}
.screen.left{left:107px}
.screen.right{left:983px}
.screen.opening{left:547px;height:1010px}
.status{position:absolute;left:23px;top:15px;font-size:11px}
.status-icons{position:absolute;right:24px;top:13px;display:flex;gap:12px}
.title{position:absolute;left:22px;top:62px;font-size:21px;font-weight:400}
.help{position:absolute;left:337px;top:66px;width:28px;height:28px;border-radius:50%;background:var(--help);color:#fff;font-size:16px;text-align:center;line-height:28px}
.card{position:absolute;left:24px;width:342px;height:128px;border:1px solid var(--line);border-radius:6px;background:#fff}
.card.raised{border-color:#eee;box-shadow:0 6px 22px rgba(90,70,160,.16)}
.avatar{position:absolute;left:14px;top:12px;width:56px;height:48px;border-radius:3px}
.av1{background:linear-gradient(#f0c49a,#2b3346)}
.av2{background:linear-gradient(#dfe6ee,#4f86b3)}
.av3{background:linear-gradient(#e9e6e1,#b43e4a)}
.av4{background:linear-gradient(#cfcac3,#f2f0ec)}
.card p{position:absolute;white-space:nowrap}
.sub{left:83px;top:15px;font-size:12px;color:var(--muted)}
.sub b{font-weight:400;color:var(--ink);margin-left:4px}
.name{left:83px;top:37px;font-size:14px;font-weight:500}
.role{left:211px;top:37px;font-size:15px;color:var(--purple)}
.badge{position:absolute;right:7px;top:8px;height:18px;padding:0 10px;border-radius:9px;color:#fff;font-size:8px;line-height:18px;font-weight:500}
.complete{background:var(--green)}.active{background:var(--blue)}.canceled{background:var(--red)}
.divide{position:absolute;left:0;right:6px;top:70px;border-top:1px solid var(--line)}
.lbl{top:81px;font-size:12px;color:var(--muted)}
.loc{left:12px}.dur{left:104px}
.val{top:99px;font-size:14px;font-weight:600}
.date{left:104px;font-size:15px;font-weight:500}
.date span{color:var(--purple)}
.edit{position:absolute;left:298px;top:88px;width:28px;height:28px;border-radius:50%;background:var(--purple-soft);display:flex;align-items:center;justify-content:center}
.nav{position:absolute;left:0;right:0;bottom:0;background:var(--nav-bg);border-top:1px solid #ebe8f2;display:flex;justify-content:space-around;padding:0 10px}
.assign .nav{top:733px}
.opening .nav{top:895px}
.nav-item{display:flex;flex-direction:column;align-items:center;gap:6px;padding-top:18px;font-size:12px;color:var(--ink)}
.nav-item.current{color:var(--purple)}
.nav-item svg{width:24px;height:24px}
.info{position:absolute;left:23px;font-size:12px;color:var(--muted)}
.info-val{position:absolute;left:127px;font-size:14px;font-weight:500;color:var(--ink)}
.box{position:absolute;left:24px;width:342px;border:1px solid var(--line);border-radius:2px}
.hint{position:absolute;font-size:10px;color:#555}
.field{position:absolute;top:762px;height:22px;border:1px solid var(--line);border-radius:2px;font-size:10px;line-height:20px;padding-left:7px;background:#fafafa}
.pick{position:absolute;right:3px;top:2px;width:16px;height:16px;border-radius:3px;background:var(--purple);display:flex;align-items:center;justify-content:center}
.btn{position:absolute;top:825px;width:96px;height:36px;color:#fff;font-size:14px;font-weight:600;text-align:center;line-height:36px}
.save{left:169px;background:var(--purple)}
.close{left:269px;background:var(--close)}
</style>
</head>
<body>
<svg width="0" height="0" style="position:absolute">
  <defs>
    <symbol id="i-wifi" viewBox="0 0 24 18"><path d="M2 6a14 14 0 0 1 20 0M5 9.5a10 10 0 0 1 14 0M8 13a5.5 5.5 0 0 1 8 0" fill="none" stroke="#111" stroke-width="1.8" stroke-linecap="round"/><circle cx="12" cy="16" r="1.4" fill="#111"/></symbol>
    <symbol id="i-batt" viewBox="0 0 26 14"><rect x="1" y="1" width="21" height="12" rx="2" fill="none" stroke="#111" stroke-width="1.5"/><rect x="4" y="4" width="3" height="6" fill="#111"/><rect x="23" y="5" width="2" height="4" fill="#111"/></symbol>
    <symbol id="i-home" viewBox="0 0 24 24"><path d="M3 11 12 4l9 7M5 9.5V20h14V9.5M10 20v-5h4v5" fill="none" stroke="currentColor" stroke-width="1.6" stroke-linejoin="round"/></symbol>
    <symbol id="i-open" viewBox="0 0 24 24"><path d="M12 2v4M5 6h14v5H5zM3 14h18v5H3zM12 11v3M12 19v3" fill="none" stroke="currentColor" stroke-width="1.6" stroke-linejoin="round"/></symbol>
    <symbol id="i-doc" viewBox="0 0 24 24"><path d="M8 3h9l3 3v13H8zM5 6v15h11M11 9h6M11 12h6M11 15h4" fill="none" stroke="currentColor" stroke-width="1.6" stroke-linejoin="round"/></symbol>
    <symbol id="i-support" viewBox="0 0 24 24"><path d="M4 14v-2a8 8 0 0 1 16 0v2M4 14h3v5H4zM17 14h3v5h-3zM20 19a3 3 0 0 1-3 3h-3" fill="none" stroke="currentColor" stroke-width="1.6" stroke-linejoin="round"/></symbol>
    <symbol id="i-logout" viewBox="0 0 24 24"><circle cx="12" cy="12" r="9" fill="none" stroke="currentColor" stroke-width="1.6"/><circle cx="12" cy="10" r="3" fill="none" stroke="currentColor" stroke-width="1.6"/><path d="M6.5 18.5a6 6 0 0 1 11 0" fill="none" stroke="currentColor" stroke-width="1.6"/></symbol>
    <symbol id="i-edit" viewBox="0 0 16 16"><path d="M3 13l1-3 7-7 2 2-7 7zM2 15h12" fill="none" stroke="#6b4fa8" stroke-width="1.3" stroke-linejoin="round"/></symbol>
    <symbol id="i-upload" viewBox="0 0 20 20"><path d="M10 13V3M6 7l4-4 4 4M3 12v5h14v-5" fill="none" stroke="#6b4fa8" stroke-width="1.5" stroke-linecap="round" stroke-linejoin="round"/></symbol>
    <symbol id="i-cal" viewBox="0 0 10 10"><rect x="1" y="2" width="8" height="7" fill="none" stroke="#fff" stroke-width="1"/><path d="M1 4h8M3 1v2M7 1v2" stroke="#fff" stroke-width="1"/></symbol>
    <symbol id="i-clock" viewBox="0 0 10 10"><circle cx="5" cy="5" r="3.5" fill="none" stroke="#fff" stroke-width="1"/><path d="M5 3v2h1.5" fill="none" stroke="#fff" stroke-width="1"/></symbol>
  </defs>
</svg>

<main class="stage">
  <!-- Assignments list screen -->
  <section class="screen assign left">
    <p class="status">10.00 Pm</p>
    <div class="status-icons"><svg width="22" height="16"><use href="#i-wifi"/></svg><svg width="24" height="13"><use href="#i-batt"/></svg></div>
    <h1 class="title">My Assignments</h1>
    <div class="help">?</div>

    <article class="card" style="top:130px">
      <div class="avatar av1" role="img" aria-label="Substitute profile photo"></div>
      <span class="badge complete">Complete</span>
      <p class="sub">Subbing For:</p><p class="name">Nora Whitfield</p><p class="role">Teacher</p>
      <div class="divide"></div>
      <p class="lbl loc">Location</p><p class="lbl dur">Duration</p>
      <p class="val loc">DVES</p><p class="val date">09/02 - 09/02 <span>(1h 0m)</span></p>
      <div class="edit"><svg width="16" height="16"><use href="#i-edit"/></svg></div>
    </article>
    <article class="card" style="top:289px">
      <div class="avatar av2" role="img" aria-label="Substitute profile photo"></div>
      <span class="badge complete">Complete</span>
      <p class="sub">Subbing For:<b>Extra Duty</b></p><p class="name">Nora Whitfield</p><p class="role">Teacher</p>
      <div class="divide"></div>
      <p class="lbl loc">Location</p><p class="lbl dur">Duration</p>
      <p class="val loc">DVES</p><p class="val date">09/02 - 09/02 <span>(1h 0m)</span></p>
      <div class="edit"><svg width="16" height="16"><use href="#i-edit"/></svg></div>
    </article>
    <article class="card raised" style="top:447px">
      <div class="avatar av3" role="img" aria-label="Substitute profile photo"></div>
      <span class="badge active">Active</span>
      <p class="sub">Subbing For:</p><p class="name">Grant Ellison</p><p class="role">Administrator</p>
      <div class="divide"></div>
      <p class="lbl loc">Location</p><p class="lbl dur">Duration</p>
      <p class="val loc">DVES</p><p class="val date">09/02 - 09/02 <span>(1h 0m)</span></p>
      <div class="edit"><svg width="16" height="16"><use href="#i-edit"/></svg></div>
    </article>
    <article class="card" style="top:606px">
      <div class="avatar av4" role="img" aria-label="Substitute profile photo"></div>
      <span class="badge canceled">Canceled</span>
      <p class="sub">Subbing For:</p><p class="name">Priya Castell</p><p class="role">Teacher</p>
      <div class="divide"></div>
      <p class="lbl loc">Location</p><p class="lbl dur">Duration</p>
      <p class="val loc">DVES</p><p class="val date">09/02 - 09/02 <span>(1h 0m)</span></p>
      <div class="edit"><svg width="16" height="16"><use href="#i-edit"/></svg></div>
    </article>

    <nav class="nav">
      <span class="nav-item"><svg><use href="#i-home"/></svg>Home</span>
      <span class="nav-item"><svg><use href="#i-open"/></svg>Opening</span>
      <span class="nav-item current"><svg><use href="#i-doc"/></svg>Assignment</span>
      <span class="nav-item"><svg><use href="#i-support"/></svg>Support</span>
      <span class="nav-item"><svg><use href="#i-logout"/></svg>Logout</span>
    </nav>
  </section>

  <!-- Opening detail screen -->
  <section class="screen opening">
    <p class="status">10.00 Pm</p>
    <div class="status-icons"><svg width="22" height="16"><use href="#i-wifi"/></svg><svg width="24" height="13"><use href="#i-batt"/></svg></div>
    <h1 class="title">Opening Info</h1>
    <div class="help">?</div>

    <p class="info" style="top:108px">Summary :</p><p class="info-val" style="top:106px">Testing-test</p>
    <p class="info" style="top:141px">Location :</p><p class="info-val" style="top:139px">Demo Valley Elementary School</p>
    <p class="info" style="top:175px">Type :</p>
    <p class="info" style="top:208px">Vacancy :</p>
    <p class="info" style="top:241px">Regular Staff :</p><p class="info-val" style="top:239px">Owen Hartley</p>
    <p class="info" style="top:275px">Category :</p><p class="info-val" style="top:273px">Teacher</p>
    <p class="info" style="top:308px">Department :</p>
    <p class="info" style="top:338px">Description</p>
    <div class="box" style="top:361px;height:124px"></div>

    <p class="info" style="top:501px">Comments</p>
    <div class="box" style="top:524px;height:71px">
      <p class="hint" style="left:12px;top:15px">Write a comment or upload a file</p>
      <svg style="position:absolute;left:307px;top:12px" width="20" height="20"><use href="#i-upload"/></svg>
    </div>

    <p class="info" style="top:611px">Additional Details</p>
    <div class="box" style="top:634px;height:71px">
      <p class="hint" style="left:12px;top:15px">Parking Spot</p>
      <div style="position:absolute;left:12px;right:16px;top:47px;border-top:1px solid #888"></div>
    </div>

    <p class="info" style="top:729px">Time Slot</p>
    <p class="info" style="top:729px;left:auto;right:24px;color:var(--ink)"><span style="color:var(--purple)">Accept</span> | Withdraw</p>

    <div class="field" style="left:24px;width:64px">Date<span class="pick"><svg width="10" height="10"><use href="#i-cal"/></svg></span></div>
    <div class="field" style="left:228px;width:64px">From<span class="pick"><svg width="10" height="10"><use href="#i-clock"/></svg></span></div>
    <div class="field" style="left:301px;width:65px">To<span class="pick"><svg width="10" height="10"><use href="#i-clock"/></svg></span></div>

    <span class="btn save">SAVE</span>
    <span class="btn close">CLOSE</span>

    <nav class="nav">
      <span class="nav-item"><svg><use href="#i-home"/></svg>Home</span>
      <span class="nav-item current"><svg><use href="#i-open"/></svg>Opening</span>
      <span class="nav-item"><svg><use href="#i-doc"/></svg>Assignment</span>
      <span class="nav-item"><svg><use href="#i-support"/></svg>Support</span>
      <span class="nav-item"><svg><use href="#i-logout"/></svg>Logout</span>
    </nav>
  </section>

  <!-- Assignments list screen, flat variant -->
  <section class="screen assign right">
    <p class="status">10.00 Pm</p>
    <div class="status-icons"><svg width="22" height="16"><use href="#i-wifi"/></svg><svg width="24" height="13"><use href="#i-batt"/></svg></div>
    <h1 class="title">My Assignments</h1>
    <div class="help">?</div>

    <article class="card" style="top:119px">
      <div class="avatar av1" role="img" aria-label="Substitute profile photo"></div>
      <span class="badge complete">Complete</span>
      <p class="sub">Subbing For:</p><p class="name">Nora Whitfield</p><p class="role">Teacher</p>
      <div class="divide"></div>
      <p class="lbl loc">Location</p><p class="lbl dur">Duration</p>
      <p class="val loc">DVES</p><p class="val date">09/02 - 09/02 <span>(1h 0m)</span></p>
      <div class="edit"><svg width="16" height="16"><use href="#i-edit"/></svg></div>
    </article>
    <article class="card" style="top:278px">
      <div class="avatar av2" role="img" aria-label="Substitute profile photo"></div>
      <span class="badge complete">Complete</span>
      <p class="sub">Subbing For:<b>Extra Duty</b></p><p class="name">Nora Whitfield</p><p class="role">Teacher</p>
      <div class="divide"></div>
      <p class="lbl loc">Location</p><p class="lbl dur">Duration</p>
      <p class="val loc">DVES</p><p class="val date">09/02 - 09/02 <span>(1h 0m)</span></p>
      <div class="edit"><svg width="16" height="16"><use href="#i-edit"/></svg></div>
    </article>
    <article class="card raised" style="top:436px">
      <div class="avatar av3" role="img" aria-label="Substitute profile photo"></div>
      <span class="badge active">Active</span>
      <p class="sub">Subbing For:</p><p class="name">Grant Ellison</p><p class="role">Administrator</p>
      <div class="divide"></div>
      <p class="lbl loc">Location</p><p class="lbl dur">Duration</p>
      <p class="val loc">DVES</p><p class="val date">09/02 - 09/02 <span>(1h 0m)</span></p>
      <div class="edit"><svg width="16" height="16"><use href="#i-edit"/></svg></div>
    </article>
    <article class="card" style="top:595px">
      <div class="avatar av4" role="img" aria-label="Substitute profile photo"></div>
      <span class="badge canceled">Canceled</span>
      <p class="sub">Subbing For:</p><p class="name">Priya Castell</p><p class="role">Teacher</p>
      <div class="divide"></div>
      <p class="lbl loc">Location</p><p class="lbl dur">Duration</p>
      <p class="val loc">DVES</p><p class="val date">09/02 - 09/02 <span>(1h 0m)</span></p>
      <div class="edit"><svg width="16" height="16"><use href="#i-edit"/></svg></div>
    </article>

    <nav class="nav">
      <span class="nav-item"><svg><use href="#i-home"/></svg>Home</span>
      <span class="nav-item"><svg><use href="#i-open"/></svg>Opening</span>
      <span class="nav-item current"><svg><use href="#i-doc"/></svg>Assignment</span>
      <span class="nav-item"><svg><use href="#i-support"/></svg>Support</span>
      <span class="nav-item"><svg><use href="#i-logout"/></svg>Logout</span>
    </nav>
  </section>
</main>
</body>
</html>
```